Business Card Design - Amberfield Court

We are looking at a new design for our business cards that has a modern and professional look. We run a residential aged care facility focussing on the care of residents. The cards will be used for potential clients, consultants and business opportunities in this sector. Blue and white is our main colours and would to see these colours incorporated in the design.
Industry/Entity Type
Business
Contact Information for Business Card
Amberfield Court, Darren Walsh, dwalsh@amberfieldcourt.com.au, Finance Manager, 0472 639 208, BCom, 37 Marrabel Crescent, Brindle Vale, Qld 4093.
Look and feel
Each slider illustrates characteristics of the customer's brand and the style your logo design should communicate.

```html
<!DOCTYPE html>
<html lang="en">
<head>
<meta charset="utf-8">
<title>Amberfield Court – Business Card</title>
<link rel="stylesheet" href="https://fonts.googleapis.com/css2?family=Arimo:ital,wght@0,400;0,700;1,400&display=swap">
<style>
  :root {
    --page: #e9e6e1;
    --blue: #4d7590;
    --blue-deep: #3e6480;
    --blue-light: #6e93aa;
    --white: #ffffff;
    --taupe: #a59a91;
    --ink: #2f2f2f;
    --grey: #8c8c8c;
  }
  * { margin: 0; padding: 0; box-sizing: border-box; }
  html, body {
    width: 1200px;
    height: 950px;
    overflow: hidden;
    background: var(--page);
    font-family: "Arimo", Arial, sans-serif;
  }
  .sheet {
    position: relative;
    width: 1200px;
    height: 950px;
  }
  .card {
    position: absolute;
    left: 240px;
    width: 720px;
    height: 440px;
    overflow: hidden;
    box-shadow: 0 6px 18px rgba(0,0,0,0.18);
  }
  .card--back { top: 30px; background: linear-gradient(135deg, var(--blue-light), var(--blue-deep)); }
  .card--front { top: 480px; background: linear-gradient(160deg, var(--blue-light), var(--blue-deep)); }
  .card svg { position: absolute; inset: 0; }

  .back-web {
    position: absolute;
    left: 0; right: 0; top: 200px;
    text-align: center;
    color: var(--white);
    font-size: 30px;
    letter-spacing: 1px;
  }

  .brand {
    position: absolute;
    left: 36px;
    top: 58px;
    display: flex;
    align-items: center;
    gap: 12px;
    color: var(--blue);
    font-size: 30px;
    font-weight: 700;
    letter-spacing: 2px;
    text-transform: uppercase;
  }
  .brand__dot {
    width: 22px; height: 22px;
    border-radius: 50%;
    background: var(--blue);
  }

  .contact {
    position: absolute;
    left: 30px;
    top: 225px;
    list-style: none;
    color: var(--ink);
    font-size: 19px;
    line-height: 30px;
  }
  .contact li { display: flex; align-items: center; gap: 8px; }
  .contact svg { position: static; width: 16px; height: 16px; flex: none; }
  .contact .contact__address { padding-left: 0; }

  .person {
    position: absolute;
    left: 440px;
    top: 175px;
  }
  .person__name {
    color: var(--blue);
    font-size: 24px;
    font-weight: 700;
    letter-spacing: 0.5px;
  }
  .person__name span { font-size: 22px; }
  .person__role {
    margin-top: 4px;
    padding-left: 18px;
    color: var(--grey);
    font-size: 19px;
  }
</style>
</head>
<body>
<main class="sheet">

  <section class="card card--back" aria-label="Business card back">
    <p class="back-web">www.amberfieldcourt.com.au</p>
  </section>

  <section class="card card--front" aria-label="Business card front">
    <svg viewBox="0 0 720 440" width="720" height="440" aria-hidden="true">
      <path d="M705 205 C703 330 615 410 470 440 H425 C600 400 705 320 705 205 Z" fill="var(--taupe)"/>
      <path d="M0 0 H360 C570 0 705 90 705 205 C705 320 600 400 425 440 H0 Z" fill="var(--white)"/>
    </svg>

    <div class="brand">
      <span class="brand__dot"></span>
      <span class="brand__name">Amberfield Court</span>
    </div>

    <ul class="contact">
      <li>
        <svg viewBox="0 0 16 16"><path d="M3 2h3l1 3-2 1.5a9 9 0 0 0 4.5 4.5L11 9l3 1v3a2 2 0 0 1-2 2A11 11 0 0 1 1 4a2 2 0 0 1 2-2z" fill="var(--blue)"/></svg>
        0472 639 208
      </li>
      <li>
        <svg viewBox="0 0 16 16"><rect x="1" y="3" width="14" height="10" fill="var(--blue)"/><path d="M1 3l7 6 7-6" stroke="#fff" stroke-width="1.4" fill="none"/></svg>
        dwalsh@amberfieldcourt.com.au
      </li>
      <li>
        <svg viewBox="0 0 16 16"><circle cx="8" cy="8" r="7" fill="var(--blue)"/><path d="M1 8h14M8 1c3 3 3 11 0 14M8 1c-3 3-3 11 0 14" stroke="#fff" stroke-width="1" fill="none"/></svg>
        www.amberfieldcourt.com.au
      </li>
      <li class="contact__address">37 Marrabel Crescent, Brindle Vale, Qld 4093.</li>
    </ul>

    <div class="person">
      <p class="person__name">Darren Walsh <span>BCom</span></p>
      <p class="person__role">Finance Manager</p>
    </div>
  </section>

</main>
</body>
</html>
```